New Fun, Positive, energised looking Business Card Needed for High Achiever Coach

I am looking for a two sided full colour business card. I am self employed and have recently re branded my 1-2-1 work re-vitalising high achievers. My target client base for these cards is therefore high achievers - usually aged 40 -55, they are often entrepreneurs, CEO or work in banking and finance and 2/3 are male. I work with them on 90 day or 6 month coaching programs to help them live their success in a healthier, more sustainable and fulfiiled way. They pay for this privately so though they are corporate types the cards need not look 'corporate'. I want to portray the idea of transformation, vitality and re-connecting.
You can get a feel for the look I like on my new website: morvenlisk.co.uk
I want to use this logo with strapline (Re-Vitalising High Achievers) (I purchased off Logoharbor) and font/ colours (the turquoise and green).
Details to include on the card:
www.morvenlisk.co.uk
+44 7915 302618
morven@morvenlisk.co.uk
skype: morvenlisk
I'd also like to include:
Do you struggle to switch off? Want to be healthier and feel fitter? Want closer relationships? More clarity over the direction you are headed? I can help you do these things using integrated mind-body techniques. Visit morvenlisk.co.uk TODAY to apply for a FREE Breakthrough session.
BUT if that is too much text for a card I am open to advice/ammendments.
Updates
Thanks for your design - I am considering them. PLease change the wording to :

```html
<!DOCTYPE html>
<html lang="en">
<head>
<meta charset="utf-8">
<title>Morven Lisk – Business Card</title>
<link href="https://fonts.googleapis.com/css2?family=Open+Sans:ital,wght@0,400;0,600;0,700;1,400&display=swap" rel="stylesheet">
<style>
  :root {
    --turquoise: #00a6c9;
    --turquoise-deep: #0096b8;
    --green: #5cb85c;
    --ink: #27444c;
    --white: #ffffff;
    --backdrop: #e9e9ee;
  }
  * { box-sizing: border-box; margin: 0; padding: 0; }
  html, body {
    width: 1200px;
    height: 987px;
    overflow: hidden;
    background: var(--backdrop);
    font-family: "Open Sans", Arial, sans-serif;
  }
  .sheet {
    width: 1200px;
    height: 987px;
    display: flex;
    flex-direction: column;
    align-items: center;
    justify-content: center;
    gap: 60px;
  }
  .card {
    position: relative;
    width: 700px;
    height: 400px;
    border-radius: 30px;
    overflow: hidden;
    box-shadow: 0 8px 24px rgba(0,0,0,0.12);
  }

  /* Front */
  .card--front { background: var(--white); }
  .front-band {
    position: absolute;
    inset: 0;
    width: 100%;
    height: 100%;
  }
  .brand {
    position: absolute;
    top: 62px;
    left: 0;
    right: 0;
    display: flex;
    flex-direction: column;
    align-items: center;
  }
  .brand-name-row {
    display: flex;
    align-items: center;
    gap: 14px;
  }
  .brand-dot {
    width: 34px;
    height: 34px;
    border-radius: 50%;
    background: var(--green);
  }
  .brand-name {
    font-weight: 700;
    font-size: 46px;
    letter-spacing: 0.5px;
    color: var(--turquoise);
  }
  .brand-strapline {
    margin-top: 2px;
    font-size: 19px;
    color: var(--turquoise);
  }
  .contacts {
    position: absolute;
    left: 40px;
    bottom: 34px;
    color: var(--white);
    font-size: 19px;
    line-height: 1.7;
  }
  .contact-row { display: flex; gap: 22px; }
  .contact-item { display: flex; align-items: center; gap: 7px; }
  .contact-icon { width: 17px; height: 17px; flex: none; }

  /* Back */
  .card--back {
    background: var(--turquoise);
    color: var(--ink);
    font-size: 17px;
    line-height: 1.4;
  }
  .questions {
    position: absolute;
    top: 38px;
    left: 44px;
    width: 330px;
  }
  .answer {
    position: absolute;
    top: 178px;
    right: 40px;
    width: 330px;
  }
  .marker { display: block; font-size: 15px; font-weight: 600; }
  .answer p + p { margin-top: 12px; }
  .site { color: var(--white); font-weight: 700; }
</style>
</head>
<body>
<main class="sheet">

  <section class="card card--front" aria-label="Card front">
    <svg class="front-band" viewBox="0 0 700 400" preserveAspectRatio="none" aria-hidden="true">
      <path d="M0,162 C240,250 470,318 700,330 L700,400 L0,400 Z" fill="var(--green)"/>
      <path d="M0,176 C240,264 470,332 700,344 L700,400 L0,400 Z" fill="var(--turquoise)"/>
    </svg>

    <div class="brand">
      <div class="brand-name-row">
        <span class="brand-dot"></span>
        <span class="brand-name">Morven Lisk</span>
      </div>
      <span class="brand-strapline">Re-Vitalising High Achievers</span>
    </div>

    <div class="contacts">
      <div class="contact-row">
        <span class="contact-item">
          <svg class="contact-icon" viewBox="0 0 20 20" aria-hidden="true"><circle cx="10" cy="10" r="9.5" fill="#fff"/><path d="M7 5l2 2.5-1.2 1.4a7 7 0 003.3 3.3l1.4-1.2L15 13l-1 2c-4.5-.3-8.7-4.5-9-9z" fill="var(--turquoise)"/></svg>
          +44 7915 302618
        </span>
        <span class="contact-item">
          <svg class="contact-icon" viewBox="0 0 20 20" aria-hidden="true"><rect x="1" y="4" width="18" height="12" rx="2" fill="#fff"/><path d="M2 5l8 6 8-6" fill="none" stroke="var(--turquoise)" stroke-width="1.6"/></svg>
          morven@morvenlisk.co.uk
        </span>
      </div>
      <div class="contact-row">
        <span class="contact-item">
          <svg class="contact-icon" viewBox="0 0 20 20" aria-hidden="true"><circle cx="10" cy="10" r="8.5" fill="none" stroke="#fff" stroke-width="1.6"/><ellipse cx="10" cy="10" rx="3.8" ry="8.5" fill="none" stroke="#fff" stroke-width="1.4"/><path d="M1.5 10h17M3 6h14M3 14h14" stroke="#fff" stroke-width="1.2"/></svg>
          www.morvenlisk.co.uk
        </span>
        <span class="contact-item">
          <span class="contact-icon" style="border-radius:50%;background:#fff;display:inline-block"></span>
          morvenlisk
        </span>
      </div>
    </div>
  </section>

  <section class="card card--back" aria-label="Card back">
    <div class="questions">
      <span class="marker">Q.</span>
      <p>Do you struggle to switch off?<br>
      Want to be healthier &amp; feel fitter?<br>
      Want closer relationships?<br>
      More clarity over the direction you are headed?</p>
    </div>
    <div class="answer">
      <span class="marker">A.</span>
      <p>I can help you do these things using integrated mind-body techniques.</p>
      <p>Visit <span class="site">morvenlisk.co.uk</span> TODAY to apply for a FREE Breakthrough session.</p>
    </div>
  </section>

</main>
</body>
</html>
```